Stylish new business card needed!

Hello everyone! I am in need of a new business card design for an alarm company here in Hurricane WV. I have all fonts, color codes and logos provided for you use! We are a young company and like the style of a clean sleek looking business card. Would like it double sided, one side holding the logo and the other with your design!
Target Market(s)
The people that are looking for the newest tech for home automation and security
Industry/Entity Type
Alarm services; Home automation
Contact Information for Business Card
Name of person; position (Sales; Installer); Phone Number (555.418.7260); Employee cell Number; Website (www.GuardedByVelk.example); Employee Email; Double sided
Look and feel
Each slider illustrates characteristics of the customer's brand and the style your logo design should communicate.

```html
<!DOCTYPE html>
<html lang="en">
<head>
<meta charset="utf-8">
<title>Velk Business Card</title>
<link rel="stylesheet" href="https://fonts.googleapis.com/css2?family=Arimo:wght@400;700&display=swap">
<style>
  :root {
    --backdrop: #2b2b2e;
    --card: #1f1f22;
    --card-edge: #141416;
    --accent: #e8782f;
    --surname: #9a9a9e;
    --text: #f1f1f1;
    --ghost: #2a2a2e;
    --ghost-accent: #2f2624;
    --logo-tone: #121214;
  }
  * { margin: 0; padding: 0; box-sizing: border-box; }
  html, body {
    width: 1200px; height: 780px; overflow: hidden;
    background: var(--backdrop);
    font-family: "Arimo", Arial, sans-serif;
  }
  .canvas { position: relative; width: 1200px; height: 780px; }
  .card {
    position: absolute; top: 230px;
    width: 540px; height: 309px;
    background: var(--card);
    box-shadow: 0 4px 0 var(--card-edge), 0 8px 0 #18181a, 0 18px 30px rgba(0,0,0,.45);
    overflow: hidden;
  }
  .card--front { left: 40px; }
  .card--back { left: 620px; }

  .front-decor { position: absolute; inset: 0; }

  .holder { position: absolute; left: 44px; top: 52px; }
  .holder__name { font-size: 30px; font-weight: 700; letter-spacing: .2px; }
  .holder__first { color: var(--accent); }
  .holder__last { color: var(--surname); }
  .holder__role { margin-top: 6px; font-size: 15px; color: var(--text); }

  .contact {
    position: absolute; left: 286px; top: 150px;
    list-style: none; color: var(--text); font-size: 16px;
  }
  .contact__item { display: flex; align-items: center; gap: 10px; height: 26px; }
  .contact__icon { width: 16px; height: 16px; flex: none; }

  .brand {
    position: absolute; inset: 0;
    display: flex; align-items: center; justify-content: center;
  }
  .brand__name {
    font-size: 110px; font-weight: 700; letter-spacing: 4px;
    color: var(--logo-tone);
  }
</style>
</head>
<body>
<main class="canvas">

  <section class="card card--front" aria-label="Business card front">
    <svg class="front-decor" width="540" height="309" viewBox="0 0 540 309" aria-hidden="true">
      <circle cx="185" cy="120" r="88" fill="none" stroke="var(--ghost-accent)" stroke-width="22"/>
      <line x1="250" y1="200" x2="330" y2="105" stroke="#cfcfcf" stroke-width="1"/>
    </svg>

    <div class="holder">
      <h1 class="holder__name"><span class="holder__first">Mara</span> <span class="holder__last">Linden</span></h1>
      <p class="holder__role">Sales; Installer</p>
    </div>

    <ul class="contact">
      <li class="contact__item">
        <svg class="contact__icon" viewBox="0 0 16 16" aria-hidden="true"><path d="M3 1.5l3 .5 1 3-2 1.5c.8 1.8 2.2 3.2 4 4L10.5 8.5l3 1 .5 3-2 1.5C6.5 13.5 2.5 9.5 1.5 3.5z" fill="var(--accent)"/></svg>
        <span>555.418.7260</span>
      </li>
      <li class="contact__item">
        <svg class="contact__icon" viewBox="0 0 16 16" aria-hidden="true"><rect x="4" y="1" width="8" height="14" rx="1.5" fill="none" stroke="var(--accent)" stroke-width="1.5"/></svg>
        <span>555.902.3318</span>
      </li>
      <li class="contact__item">
        <svg class="contact__icon" viewBox="0 0 16 16" aria-hidden="true"><circle cx="8" cy="8" r="6.5" fill="none" stroke="var(--accent)" stroke-width="1.5"/><path d="M1.5 8h13M8 1.5c-3 3.5-3 9.5 0 13M8 1.5c3 3.5 3 9.5 0 13" fill="none" stroke="var(--accent)" stroke-width="1.2"/></svg>
        <span>www.GuardedByVelk.example</span>
      </li>
      <li class="contact__item">
        <svg class="contact__icon" viewBox="0 0 16 16" aria-hidden="true"><rect x="1" y="3" width="14" height="10" rx="1" fill="var(--accent)"/><path d="M1.5 3.5L8 9l6.5-5.5" fill="none" stroke="var(--card)" stroke-width="1.3"/></svg>
        <span>info@GuardedByVelk.example</span>
      </li>
    </ul>
  </section>

  <section class="card card--back" aria-label="Business card back">
    <div class="brand">
      <span class="brand__name">VELK</span>
    </div>
  </section>

</main>
</body>
</html>
```